Automotive component supplier needs a business card design

We need a business card design for our company called Velran Global Components Ltd based in the UK. We are a supplier of interior and exterior components to premium car manufacturers such as Corvel Ashby, Hadley Fenn, Marquist and Tavarelli. We would like to see a modern business card design that uses the colour blue.

Target Market(s)

Premium automotive car manufacturers.

Industry/Entity Type

Automotive

Contact Information for Business Card

Company Name : Velran Global Components Limited
Address: 17 Marlow Yard, Upper Heath, Warwick, CV31 8QL, United Kingdom
Web Address : www.velrancomponents-example.co.uk

Font styles to use
Other font styles liked:
• Helvetica

Colors
3176b5
0255a3
85acd3
cfdeed
cee9f5
85cae6
34a6d7
0692cd
9bcb3c

Requirements
Must have
• Clear company logo and a mixture of blue colours.
Nice to have
• A high quality modern image.
Should not have
• Multiple colours.

```html
<!DOCTYPE html>
<html lang="en">
<head>
<meta charset="utf-8">
<title>Velran Global Components – Business Card</title>
<link rel="stylesheet" href="https://fonts.googleapis.com/css2?family=Montserrat:wght@400;500;600;700;800&display=swap">
<style>
  :root {
    --blue-deep: #0255a3;
    --blue-mid: #3176b5;
    --blue-bright: #0692cd;
    --blue-sky: #34a6d7;
    --green: #9bcb3c;
    --white: #ffffff;
    --text-blue: #1f6fc0;
    --backdrop: #2a2a2a;
  }
  * { box-sizing: border-box; margin: 0; padding: 0; }
  html, body {
    width: 1200px; height: 1000px; overflow: hidden;
    background: var(--backdrop);
    font-family: "Montserrat", Helvetica, Arial, sans-serif;
  }
  .stage { position: relative; width: 1200px; height: 1000px; }
  .card {
    position: absolute; left: 300px;
    width: 600px; height: 343px;
    border-radius: 20px; overflow: hidden;
    box-shadow: 0 18px 40px rgba(0,0,0,.45);
  }
  .card-front {
    top: 120px;
    background: radial-gradient(ellipse at 55% 40%, #2f8fd6 0%, #1b6fc2 55%, var(--blue-deep) 100%);
  }
  .card-back {
    top: 520px;
    background: radial-gradient(ellipse at 40% 30%, #3b9be0 0%, #1e72c4 55%, var(--blue-deep) 100%);
  }
  .wordmark {
    position: absolute; color: var(--white); font-weight: 800;
    display: flex; align-items: center; gap: 14px;
  }
  .wordmark-mark { width: 16px; height: 16px; background: var(--green); flex: none; }
  .wordmark-text { display: flex; flex-direction: column; line-height: 1; }
  .wordmark-name { font-size: 64px; letter-spacing: 3px; }
  .wordmark-sub { font-size: 15px; letter-spacing: 2.6px; margin-top: 8px; }
  .card-front .wordmark { left: 130px; top: 125px; }
  .card-back .wordmark { left: 30px; top: 92px; gap: 12px; }
  .card-back .wordmark-mark { width: 13px; height: 13px; }
  .card-back .wordmark-name { font-size: 42px; letter-spacing: 1px; }
  .card-back .wordmark-sub { font-size: 10px; letter-spacing: 1.6px; margin-top: 6px; }
  .back-curve { position: absolute; inset: 0; width: 600px; height: 343px; }
  .contact {
    position: absolute; right: 26px; top: 44px; width: 300px;
    text-align: right; color: var(--text-blue);
  }
  .contact-head { display: flex; justify-content: flex-end; align-items: flex-start; gap: 8px; }
  .contact-name { font-size: 21px; font-weight: 600; letter-spacing: .5px; line-height: 1; }
  .contact-tag { width: 16px; height: 24px; background: var(--green); margin-top: -4px; margin-right: -26px; }
  .contact-role { color: var(--green); font-size: 12px; margin-top: 4px; }
  .contact-address { font-size: 11.5px; line-height: 1.35; margin-top: 14px; }
  .contact-lines { list-style: none; margin-top: 4px; font-size: 11.5px; line-height: 1.45; }
  .contact-lines li { display: flex; justify-content: flex-end; align-items: center; gap: 8px; }
  .contact-lines svg { width: 10px; height: 10px; flex: none; }
</style>
</head>
<body>
<main class="stage">

  <section class="card card-front" aria-label="Business card front">
    <div class="wordmark">
      <span class="wordmark-mark"></span>
      <div class="wordmark-text">
        <span class="wordmark-name">VELRAN</span>
        <span class="wordmark-sub">GLOBAL COMPONENTS</span>
      </div>
    </div>
  </section>

  <section class="card card-back" aria-label="Business card back">
    <svg class="back-curve" viewBox="0 0 600 343" aria-hidden="true">
      <path d="M340 0 C 262 70, 262 250, 372 343 L 600 343 L 600 0 Z" fill="var(--green)"/>
      <path d="M350 0 C 272 70, 272 250, 382 343 L 600 343 L 600 0 Z" fill="var(--white)"/>
    </svg>

    <div class="wordmark">
      <span class="wordmark-mark"></span>
      <div class="wordmark-text">
        <span class="wordmark-name">VELRAN</span>
        <span class="wordmark-sub">GLOBAL COMPONENTS</span>
      </div>
    </div>

    <div class="contact">
      <div class="contact-head">
        <span class="contact-name">TOMAS REEVE</span>
        <span class="contact-tag"></span>
      </div>
      <p class="contact-role">Director</p>
      <p class="contact-address">17 Marlow Yard<br>Upper Heath, Warwick<br>CV31 8QL, United Kingdom</p>
      <ul class="contact-lines">
        <li>+330 2518-4406
          <svg viewBox="0 0 10 10"><path d="M2 1 L4 1 L4.6 3 L3.4 3.8 Q4.4 5.8 6.2 6.6 L7 5.4 L9 6 L9 8 Q5 9 2.4 6 Q1 4 2 1Z" fill="var(--green)"/></svg></li>
        <li>+330 2593-1172
          <svg viewBox="0 0 10 10"><rect x="2.5" y="0.5" width="5" height="9" rx="1" fill="none" stroke="var(--green)"/><circle cx="5" cy="7.8" r=".6" fill="var(--green)"/></svg></li>
        <li>info@velrancomponents-example.co.uk
          <svg viewBox="0 0 10 10"><rect x=".5" y="2" width="9" height="6" fill="none" stroke="var(--green)"/><path d="M.5 2 L5 5.5 L9.5 2" fill="none" stroke="var(--green)"/></svg></li>
        <li>www.velrancomponents-example.co.uk
          <svg viewBox="0 0 10 10"><circle cx="5" cy="5" r="4.3" fill="none" stroke="var(--green)"/><ellipse cx="5" cy="5" rx="1.8" ry="4.3" fill="none" stroke="var(--green)"/><path d="M.7 5 H9.3" stroke="var(--green)"/></svg></li>
      </ul>
    </div>
  </section>

</main>
</body>
</html>
```